Business Card Design for Software Development Company

I am looking for a business card design the incorporates my new logo (attached below).

Key information to include:
Name: Martin Quelbrook
Title: CEO
Email: martin@brightwellcivic.example
Phone: 555-218-9403
Website: www.brightwellcivic.example

NOTE: This design should be easy to edit so that we can order cards for different members of our team.

```html
<!DOCTYPE html>
<html lang="en">
<head>
<meta charset="utf-8">
<title>Brightwell Labs — Business Card</title>
<link href="https://fonts.googleapis.com/css2?family=Montserrat:wght@400;500;600;700&display=swap" rel="stylesheet">
<style>
  :root {
    --backdrop: #bdbdbd;
    --card-white: #ffffff;
    --navy: #363f56;
    --orange: #e2532a;
    --teal: #12806c;
    --text-light: #ffffff;
    --shadow: rgba(0, 0, 0, 0.28);
  }
  * { box-sizing: border-box; margin: 0; padding: 0; }
  html, body {
    width: 1200px;
    height: 815px;
    overflow: hidden;
  }
  body {
    background: var(--backdrop);
    font-family: "Montserrat", Arial, sans-serif;
    display: flex;
    align-items: center;
    justify-content: center;
    gap: 40px;
  }
  .card {
    position: relative;
    width: 540px;
    height: 309px;
    border-radius: 22px;
    overflow: hidden;
    box-shadow: 0 14px 30px var(--shadow);
  }

  /* Front */
  .card--front { background: var(--card-white); }
  .front-curve {
    position: absolute;
    inset: 0;
    width: 100%;
    height: 100%;
  }
  .front-curve .navy-field { fill: var(--navy); }
  .front-curve .stripe-orange { fill: none; stroke: var(--orange); stroke-width: 7; }
  .front-curve .stripe-teal { fill: var(--teal); }

  .brand {
    position: absolute;
    display: flex;
    align-items: flex-start;
    gap: 10px;
  }
  .brand__mark {
    width: 14px;
    height: 14px;
    background: var(--orange);
    flex: none;
  }
  .brand__text {
    display: flex;
    flex-direction: column;
    align-items: flex-end;
  }
  .brand__name {
    font-weight: 700;
    letter-spacing: -0.5px;
    line-height: 1;
    white-space: nowrap;
  }
  .brand__tagline {
    font-weight: 600;
    text-transform: uppercase;
    white-space: nowrap;
  }

  .card--front .brand { left: 34px; top: 112px; }
  .card--front .brand__mark { margin-top: 10px; }
  .card--front .brand__name { font-size: 32px; color: var(--navy); }
  .card--front .brand__tagline {
    margin-top: 6px;
    font-size: 6px; letter-spacing: 0.6px; color: var(--navy);
  }

  .holder {
    position: absolute;
    right: 30px;
    top: 34px;
    text-align: right;
    color: var(--navy);
  }
  .holder__name {
    font-size: 19px;
    font-weight: 600;
    letter-spacing: 1px;
    text-transform: uppercase;
  }
  .holder__title {
    font-size: 13px;
    font-weight: 400;
    letter-spacing: 1px;
    margin-top: 2px;
  }

  .contact-list {
    position: absolute;
    right: 26px;
    bottom: 40px;
    list-style: none;
    color: var(--text-light);
    font-size: 14px;
    font-weight: 400;
    text-align: right;
  }
  .contact-list li {
    display: flex;
    align-items: center;
    justify-content: flex-end;
    gap: 10px;
    margin-top: 9px;
  }
  .contact-icon { width: 12px; height: 12px; flex: none; }
  .contact-icon * { fill: var(--orange); }

  /* Back */
  .card--back { background: var(--navy); }
  .card--back .brand {
    left: 50%;
    top: 50%;
    transform: translate(-50%, -50%);
    align-items: flex-start;
  }
  .card--back .brand__mark { width: 18px; height: 18px; margin-top: 20px; }
  .card--back .brand__name { font-size: 46px; color: var(--text-light); }
  .card--back .brand__tagline {
    margin-top: 8px;
    font-size: 7.5px; letter-spacing: 0.8px; color: var(--text-light);
  }
</style>
</head>
<body>

  <section class="card card--front" aria-label="Business card front">
    <svg class="front-curve" viewBox="0 0 540 309" preserveAspectRatio="none" aria-hidden="true">
      <path class="navy-field" d="M540 104 C430 116 330 146 292 196 C254 246 200 292 166 309 L540 309 Z"/>
      <path class="stripe-orange" d="M540 90 C425 102 320 134 280 186 C242 236 186 286 150 309"/>
      <path class="stripe-teal" d="M284 166 C250 210 182 280 124 309 L140 309 C178 286 238 232 284 166 Z"/>
    </svg>

    <div class="brand">
      <span class="brand__mark"></span>
      <div class="brand__text">
        <span class="brand__name">Brightwell Labs</span>
        <span class="brand__tagline">A division of Brightwell Civic</span>
      </div>
    </div>

    <div class="holder">
      <p class="holder__name">Martin Quelbrook</p>
      <p class="holder__title">CEO</p>
    </div>

    <ul class="contact-list">
      <li>555-218-9403
        <svg class="contact-icon" viewBox="0 0 12 12" aria-hidden="true"><path d="M2.5 0.5 L4.5 0.5 L5.2 3.2 L3.8 4.3 C4.5 5.8 6 7.4 7.7 8.2 L8.8 6.8 L11.5 7.5 L11.5 9.5 C11.5 10.6 10.6 11.5 9.5 11.5 C4.5 11.2 0.8 7.5 0.5 2.5 C0.5 1.4 1.4 0.5 2.5 0.5 Z"/></svg>
      </li>
      <li>martin@brightwellcivic.example
        <svg class="contact-icon" viewBox="0 0 12 12" aria-hidden="true"><path d="M0 2 H12 V10 H0 Z M0.8 2.6 L6 6.6 L11.2 2.6 Z" fill-rule="evenodd"/></svg>
      </li>
      <li>www.brightwellcivic.example
        <svg class="contact-icon" viewBox="0 0 12 12" aria-hidden="true"><circle cx="6" cy="6" r="6"/></svg>
      </li>
    </ul>
  </section>

  <section class="card card--back" aria-label="Business card back">
    <div class="brand">
      <span class="brand__mark"></span>
      <div class="brand__text">
        <span class="brand__name">Brightwell Labs</span>
        <span class="brand__tagline">A division of Brightwell Civic</span>
      </div>
    </div>
  </section>

</body>
</html>
```